Detail Shop Business card design

i need a business card design for my new detailing company called 'Brisk's Polish Works'. i want an all black and white design . simple, direct and to the point. i want the designer to choose a fitting font to match the logothe front should have logo, address, phone and email and the back side should have a slogan and text indicating that we offer services on anything including cars, trucks, motorcycles and RVs. slogan will read "we take pride in your ride"
maybe also very small on the back side the IG icon with Brisks_Polish_Works

phone 208.417.6352
address 3847 E Larkin Ave
Spokane WA 99214
email: BrisksPolish@mailvexo.com

Target Market(s)

all ages , auto enthusiasts

Industry/Entity Type

Automotive

Contact Information for Business Card

the front should have logo, address, phone and email and the back side should have a slogan and text indicating that we offer services on anything including cars, trucks, motorcycles and RVs. slogan will read "we take pride in your ride"

phone 208.417.6352
address 3847 E Larkin Ave
Spokane WA 99214

Colors
000000
ffffff

Requirements
Must have
• bold font and very simple design with good spacing
Nice to have
• anything creative from the designer indicating we service any types of vehicles
Should not have
• any colors ,

```html
<!DOCTYPE html>
<html lang="en">
<head>
<meta charset="utf-8">
<title>Brisk's Polish Works – Business Card</title>
<link rel="stylesheet" href="https://fonts.googleapis.com/css2?family=Bitter:wght@400;600&display=swap">
<style>
  :root {
    --backdrop: #1c1c1c;
    --card: #0e0e0e;
    --ink-bright: #e6e6e6;
    --ink-soft: #b5b5b5;
    --ink-deep: #4a4a4a;
    --rule: #6e6e6e;
  }
  * { margin: 0; padding: 0; box-sizing: border-box; }
  html, body {
    width: 1200px; height: 900px; overflow: hidden;
    background: var(--backdrop);
    font-family: "Bitter", Georgia, serif;
  }
  .sheet {
    width: 1200px; height: 900px;
    display: flex; flex-direction: column;
    align-items: center; justify-content: center; gap: 44px;
  }
  .card {
    width: 680px; height: 388px;
    background: var(--card);
    position: relative;
    box-shadow: 0 10px 30px rgba(0,0,0,.5);
  }
  /* front */
  .card-front .brand-mark {
    position: absolute; left: 0; right: 0; top: 110px;
    display: flex; flex-direction: column; align-items: center; gap: 18px;
  }
  .brand-dot {
    width: 56px; height: 56px; border-radius: 50%;
    border: 3px solid var(--ink-soft);
  }
  .brand-name {
    font-size: 30px; font-weight: 600; letter-spacing: 1px;
    color: var(--ink-soft);
  }
  .services {
    position: absolute; left: 0; right: 0; bottom: 46px;
    text-align: center; font-size: 15px; letter-spacing: 2px;
    color: var(--ink-deep); text-transform: uppercase;
  }
  /* back */
  .card-back .brand-name-muted {
    position: absolute; left: 40px; top: 150px; width: 240px;
    text-align: center; font-size: 24px; font-weight: 600;
    color: var(--ink-deep); line-height: 1.3;
  }
  .divider {
    position: absolute; left: 312px; top: 70px;
    width: 2px; height: 200px; background: var(--rule);
  }
  .contact {
    position: absolute; left: 348px; top: 78px; color: var(--ink-soft);
  }
  .contact .person { font-size: 26px; font-weight: 600; letter-spacing: 1.5px; color: var(--ink-bright); text-transform: uppercase; }
  .contact .role { font-size: 15px; margin-bottom: 18px; }
  .contact .address { font-size: 18px; line-height: 1.35; margin-bottom: 16px; letter-spacing: .5px; }
  .contact .line { display: flex; align-items: center; gap: 10px; font-size: 18px; line-height: 1.45; }
  .contact svg { width: 12px; height: 12px; fill: none; stroke: var(--ink-soft); stroke-width: 1.6; }
  .slogan {
    position: absolute; left: 0; right: 0; bottom: 44px;
    text-align: center; font-size: 19px; letter-spacing: 2px;
    color: var(--ink-deep); text-transform: uppercase; font-weight: 600;
  }
</style>
</head>
<body>
<main class="sheet">
  <section class="card card-front">
    <div class="brand-mark">
      <span class="brand-dot"></span>
      <span class="brand-name">Brisk's Polish Works</span>
    </div>
    <p class="services">Cars – Trucks – Motorcycles and RVs</p>
  </section>

  <section class="card card-back">
    <p class="brand-name-muted">Brisk's Polish Works</p>
    <span class="divider"></span>
    <div class="contact">
      <p class="person">Dorian Hale</p>
      <p class="role">Director</p>
      <p class="address">3847 E Larkin Ave<br>Spokane WA 99214</p>
      <p class="line">
        <svg viewBox="0 0 12 12"><path d="M2 1.5h2l1 2.5-1.3 1a6 6 0 0 0 3.3 3.3l1-1.3 2.5 1v2a1 1 0 0 1-1 1A9 9 0 0 1 1 2.5a1 1 0 0 1 1-1z"/></svg>
        208.417.6352
      </p>
      <p class="line">
        <svg viewBox="0 0 12 12"><rect x="1" y="2.5" width="10" height="7"/><path d="M1 2.5l5 4 5-4"/></svg>
        BrisksPolish@mailvexo.com
      </p>
      <p class="line">
        <svg viewBox="0 0 12 12"><circle cx="6" cy="6" r="5"/><path d="M1 6h10M6 1c2.5 2.7 2.5 7.3 0 10M6 1c-2.5 2.7-2.5 7.3 0 10"/></svg>
        www.BrisksPolish.com
      </p>
    </div>
    <p class="slogan">We take pride in your ride</p>
  </section>
</main>
</body>
</html>
```